Non-Fiction Book Cover Series Concepts

I need front cover concepts for a non-fiction business book series. Just concepts at this stage to show to backers (full cover designs later).

The books are for leaders and business owners. A mature, sophisticated market, AND, bold and innovative.

The series needs to be extensible - the concepts need to be able to work across at least 40 books. I am happy with a colour theme, or contrasts, or icon theme, there is no limitation to the imagination.

The books need to look like they belong to a series and to also stand alone.

I prefer simple and bold.

Imagine the Harrowfield business series (https://www.harrowfield-example.co.uk/series/bes/harrowfield-business-experts-series.html) - but I hate these designs (the colours don't work for me).

The imprint is ThoughtfulVantageBooks.example - the logo mark for the imprint is attached.

The books will be printed and ebooks - the printed version will be 5 inches by 8 inches form factor. They will be printed with a matt cover.

IF YOU WANT A BOOK TITLE TO TRY, use this:

Steady Momentum: Apply the R.U.N. Model to Inspire, Develop and Keep Talent

Thank you for your interest!

Target Market(s)

Business owners, leaders, entrepreneurs

Industry/Entity Type

Leadership

Font styles to use
Serif
Sans Serif

Requirements
Must have
• Extensible - the concept can work for many books and ALL books look part of the series
Nice to have
• I prefer simple, icons rather than photos
Should not have
• No photographic designs - icon, drawing

```html
<!DOCTYPE html>
<html lang="en">
<head>
<meta charset="utf-8">
<title>Steady Momentum – Series Cover Concepts</title>
<link rel="stylesheet" href="https://fonts.googleapis.com/css2?family=Lato:wght@300;400;900&display=swap">
<style>
  :root {
    --ink: #000000;
    --paper: #ffffff;
    --accent: #5a3ee8;
    --disc: rgba(255,255,255,0.62);
    --g1: linear-gradient(160deg, #3fc35f 0%, #6fdcb0 45%, #8ff6f6 100%);
    --g2: linear-gradient(165deg, #f35fe6 0%, #d15fe0 45%, #3a22c8 100%);
    --g3: linear-gradient(160deg, #2cc6f2 0%, #a6de60 50%, #f0e62a 100%);
    --g4: linear-gradient(170deg, #14238a 0%, #2b3cd6 45%, #9a64e6 100%);
    --g5: linear-gradient(170deg, #e02a1e 0%, #e0703a 40%, #9cc83a 75%, #d08a30 100%);
    --g6: linear-gradient(165deg, #2a3ab8 0%, #c0407a 45%, #f0602a 100%);
    --g7: linear-gradient(200deg, #f02a5a 0%, #b06080 40%, #12f090 100%);
    --g8: linear-gradient(175deg, #2aa6f0 0%, #d08a9a 50%, #f57a12 100%);
    --g9: linear-gradient(170deg, #f0d870 0%, #e070c0 45%, #7a10e6 100%);
    --g10: linear-gradient(150deg, #86f020 0%, #5cc830 40%, #4432c0 100%);
  }
  * { box-sizing: border-box; margin: 0; padding: 0; }
  html, body {
    width: 1200px; height: 768px; overflow: hidden;
    background: var(--paper);
    font-family: "Lato", Arial, sans-serif;
  }
  .series-board {
    width: 1200px; height: 768px;
    display: grid;
    grid-template-columns: repeat(5, 234px);
    grid-template-rows: repeat(2, 380px);
    column-gap: 7.5px; row-gap: 8px;
  }
  .cover {
    position: relative; overflow: hidden;
  }
  .cover-art { position: absolute; inset: 0; }
  .concept-number {
    position: absolute; left: -1px; top: -9px; z-index: 3;
    font-size: 46px; font-weight: 400; color: var(--ink); line-height: 1;
  }
  .imprint-tab {
    position: absolute; left: 27px; right: -10px; top: 19px; height: 16px;
    background: var(--paper); border-radius: 8px 0 0 8px;
    display: flex; align-items: center; gap: 6px; padding-left: 12px;
    font-size: 10px; font-weight: 400; color: var(--accent); letter-spacing: 0.1px;
  }
  .imprint-dot { width: 8px; height: 8px; border-radius: 50%; background: var(--accent); }
  .title-rings { position: absolute; left: 0; top: 70px; width: 234px; height: 248px; }
  .title-block {
    position: absolute; left: 0; right: 0; top: 142px;
    text-align: center; color: var(--ink); z-index: 2;
  }
  .series-title { font-weight: 900; font-size: 17.5px; line-height: 24px; letter-spacing: -0.2px; }
  .subtitle { font-weight: 300; font-size: 22px; line-height: 27px; white-space: nowrap; }
  .subtitle small { font-size: 10px; }
  .author-pill {
    position: absolute; left: 16px; width: 210px; top: 339px; height: 32px;
    background: var(--paper); border-radius: 16px;
    display: flex; align-items: center; justify-content: center;
    font-size: 16.5px; font-weight: 400; color: var(--accent); letter-spacing: 0.2px;
  }
</style>
</head>
<body>
<main class="series-board">
  <!-- repeated cover unit -->
  <section class="cover">
    <div class="cover-art" role="img" aria-label="Green to cyan gradient with white spirograph line pattern" style="background: var(--g1)"></div>
    <div class="concept-number">1</div>
    <div class="imprint-tab">THOUGHTFULVANTAGE <span class="imprint-dot"></span></div>
    <svg class="title-rings" viewBox="0 0 234 248"><circle cx="117" cy="124" r="103" fill="var(--disc)"/><g fill="none" stroke="#fff" stroke-width="1.6"><circle cx="118" cy="122" r="112"/><circle cx="115" cy="125" r="116"/><circle cx="120" cy="126" r="109"/><circle cx="117" cy="124" r="104"/></g></svg>
    <div class="title-block"><div class="series-title">STEADY MOMENTUM:</div><div class="subtitle"><small>Apply the</small> R.U.N. Model</div><div class="subtitle"><small>to</small> Inspire, Develop <small>and</small></div><div class="subtitle">Keep Talent</div></div>
    <div class="author-pill">AUTHOR NAME</div>
  </section>
  <section class="cover">
    <div class="cover-art" role="img" aria-label="Pink to violet gradient with white looping line pattern" style="background: var(--g2)"></div>
    <div class="concept-number">2</div>
    <div class="imprint-tab">THOUGHTFULVANTAGE <span class="imprint-dot"></span></div>
    <svg class="title-rings" viewBox="0 0 234 248"><circle cx="117" cy="124" r="103" fill="var(--disc)"/><g fill="none" stroke="#fff" stroke-width="1.6"><circle cx="118" cy="122" r="112"/><circle cx="115" cy="125" r="116"/><circle cx="120" cy="126" r="109"/><circle cx="117" cy="124" r="104"/></g></svg>
    <div class="title-block"><div class="series-title">STEADY MOMENTUM:</div><div class="subtitle"><small>Apply the</small> R.U.N. Model</div><div class="subtitle"><small>to</small> Inspire, Develop <small>and</small></div><div class="subtitle">Keep Talent</div></div>
    <div class="author-pill">AUTHOR NAME</div>
  </section>
  <section class="cover">
    <div class="cover-art" role="img" aria-label="Cyan to yellow gradient with white star spiral pattern" style="background: var(--g3)"></div>
    <div class="concept-number">3</div>
    <div class="imprint-tab">THOUGHTFULVANTAGE <span class="imprint-dot"></span></div>
    <svg class="title-rings" viewBox="0 0 234 248"><circle cx="117" cy="124" r="103" fill="var(--disc)"/><g fill="none" stroke="#fff" stroke-width="1.6"><circle cx="118" cy="122" r="112"/><circle cx="115" cy="125" r="116"/><circle cx="120" cy="126" r="109"/><circle cx="117" cy="124" r="104"/></g></svg>
    <div class="title-block"><div class="series-title">STEADY MOMENTUM:</div><div class="subtitle"><small>Apply the</small> R.U.N. Model</div><div class="subtitle"><small>to</small> Inspire, Develop <small>and</small></div><div class="subtitle">Keep Talent</div></div>
    <div class="author-pill">AUTHOR NAME</div>
  </section>
  <section class="cover">
    <div class="cover-art" role="img" aria-label="Deep blue to purple gradient with nested square line pattern" style="background: var(--g4)"></div>
    <div class="concept-number">4</div>
    <div class="imprint-tab">THOUGHTFULVANTAGE <span class="imprint-dot"></span></div>
    <svg class="title-rings" viewBox="0 0 234 248"><circle cx="117" cy="124" r="103" fill="var(--disc)"/><g fill="none" stroke="#fff" stroke-width="1.6"><circle cx="118" cy="122" r="112"/><circle cx="115" cy="125" r="116"/><circle cx="120" cy="126" r="109"/><circle cx="117" cy="124" r="104"/></g></svg>
    <div class="title-block"><div class="series-title">STEADY MOMENTUM:</div><div class="subtitle"><small>Apply the</small> R.U.N. Model</div><div class="subtitle"><small>to</small> Inspire, Develop <small>and</small></div><div class="subtitle">Keep Talent</div></div>
    <div class="author-pill">AUTHOR NAME</div>
  </section>
  <section class="cover">
    <div class="cover-art" role="img" aria-label="Red to green and amber gradient with triangle spiral line pattern" style="background: var(--g5)"></div>
    <div class="concept-number">5</div>
    <div class="imprint-tab">THOUGHTFULVANTAGE <span class="imprint-dot"></span></div>
    <svg class="title-rings" viewBox="0 0 234 248"><circle cx="117" cy="124" r="103" fill="var(--disc)"/><g fill="none" stroke="#fff" stroke-width="1.6"><circle cx="118" cy="122" r="112"/><circle cx="115" cy="125" r="116"/><circle cx="120" cy="126" r="109"/><circle cx="117" cy="124" r="104"/></g></svg>
    <div class="title-block"><div class="series-title">STEADY MOMENTUM:</div><div class="subtitle"><small>Apply the</small> R.U.N. Model</div><div class="subtitle"><small>to</small> Inspire, Develop <small>and</small></div><div class="subtitle">Keep Talent</div></div>
    <div class="author-pill">AUTHOR NAME</div>
  </section>
  <section class="cover">
    <div class="cover-art" role="img" aria-label="Blue to orange gradient with rounded spirograph loop pattern" style="background: var(--g6)"></div>
    <div class="concept-number">6</div>
    <div class="imprint-tab">THOUGHTFULVANTAGE <span class="imprint-dot"></span></div>
    <svg class="title-rings" viewBox="0 0 234 248"><circle cx="117" cy="124" r="103" fill="var(--disc)"/><g fill="none" stroke="#fff" stroke-width="1.6"><circle cx="118" cy="122" r="112"/><circle cx="115" cy="125" r="116"/><circle cx="120" cy="126" r="109"/><circle cx="117" cy="124" r="104"/></g></svg>
    <div class="title-block"><div class="series-title">STEADY MOMENTUM:</div><div class="subtitle"><small>Apply the</small> R.U.N. Model</div><div class="subtitle"><small>to</small> Inspire, Develop <small>and</small></div><div class="subtitle">Keep Talent</div></div>
    <div class="author-pill">AUTHOR NAME</div>
  </section>
  <section class="cover">
    <div class="cover-art" role="img" aria-label="Crimson to mint green gradient with star spiral line pattern" style="background: var(--g7)"></div>
    <div class="concept-number">7</div>
    <div class="imprint-tab">THOUGHTFULVANTAGE <span class="imprint-dot"></span></div>
    <svg class="title-rings" viewBox="0 0 234 248"><circle cx="117" cy="124" r="103" fill="var(--disc)"/><g fill="none" stroke="#fff" stroke-width="1.6"><circle cx="118" cy="122" r="112"/><circle cx="115" cy="125" r="116"/><circle cx="120" cy="126" r="109"/><circle cx="117" cy="124" r="104"/></g></svg>
    <div class="title-block"><div class="series-title">STEADY MOMENTUM:</div><div class="subtitle"><small>Apply the</small> R.U.N. Model</div><div class="subtitle"><small>to</small> Inspire, Develop <small>and</small></div><div class="subtitle">Keep Talent</div></div>
    <div class="author-pill">AUTHOR NAME</div>
  </section>
  <section class="cover">
    <div class="cover-art" role="img" aria-label="Sky blue to orange gradient with star spiral line pattern" style="background: var(--g8)"></div>
    <div class="concept-number">8</div>
    <div class="imprint-tab">THOUGHTFULVANTAGE <span class="imprint-dot"></span></div>
    <svg class="title-rings" viewBox="0 0 234 248"><circle cx="117" cy="124" r="103" fill="var(--disc)"/><g fill="none" stroke="#fff" stroke-width="1.6"><circle cx="118" cy="122" r="112"/><circle cx="115" cy="125" r="116"/><circle cx="120" cy="126" r="109"/><circle cx="117" cy="124" r="104"/></g></svg>
    <div class="title-block"><div class="series-title">STEADY MOMENTUM:</div><div class="subtitle"><small>Apply the</small> R.U.N. Model</div><div class="subtitle"><small>to</small> Inspire, Develop <small>and</small></div><div class="subtitle">Keep Talent</div></div>
    <div class="author-pill">AUTHOR NAME</div>
  </section>
  <section class="cover">
    <div class="cover-art" role="img" aria-label="Pale gold to violet gradient with looping spirograph pattern" style="background: var(--g9)"></div>
    <div class="concept-number">9</div>
    <div class="imprint-tab">THOUGHTFULVANTAGE <span class="imprint-dot"></span></div>
    <svg class="title-rings" viewBox="0 0 234 248"><circle cx="117" cy="124" r="103" fill="var(--disc)"/><g fill="none" stroke="#fff" stroke-width="1.6"><circle cx="118" cy="122" r="112"/><circle cx="115" cy="125" r="116"/><circle cx="120" cy="126" r="109"/><circle cx="117" cy="124" r="104"/></g></svg>
    <div class="title-block"><div class="series-title">STEADY MOMENTUM:</div><div class="subtitle"><small>Apply the</small> R.U.N. Model</div><div class="subtitle"><small>to</small> Inspire, Develop <small>and</small></div><div class="subtitle">Keep Talent</div></div>
    <div class="author-pill">AUTHOR NAME</div>
  </section>
  <section class="cover">
    <div class="cover-art" role="img" aria-label="Lime green to indigo gradient with starburst line pattern" style="background: var(--g10)"></div>
    <div class="concept-number">10</div>
    <div class="imprint-tab">THOUGHTFULVANTAGE <span class="imprint-dot"></span></div>
    <svg class="title-rings" viewBox="0 0 234 248"><circle cx="117" cy="124" r="103" fill="var(--disc)"/><g fill="none" stroke="#fff" stroke-width="1.6"><circle cx="118" cy="122" r="112"/><circle cx="115" cy="125" r="116"/><circle cx="120" cy="126" r="109"/><circle cx="117" cy="124" r="104"/></g></svg>
    <div class="title-block"><div class="series-title">STEADY MOMENTUM:</div><div class="subtitle"><small>Apply the</small> R.U.N. Model</div><div class="subtitle"><small>to</small> Inspire, Develop <small>and</small></div><div class="subtitle">Keep Talent</div></div>
    <div class="author-pill">AUTHOR NAME</div>
  </section>
</main>
</body>
</html>
```